Stationery for a private security company, "Brenmoor Security Services Ltd."

Needed is a stationery design for a private security company. The designs must show professionalism and that our company mean nothing but business. Watermark of the company logo on the letterhead page is also a must. The final design must represent innovation and professionalism. It would be great if designers could integrate the colours black and silver onto the cards and letterheads..

Thank you

```html
<!DOCTYPE html>
<html lang="en">
<head>
<meta charset="utf-8">
<title>Brenmoor Security Services Ltd. — Stationery</title>
<link href="https://fonts.googleapis.com/css2?family=Open+Sans:wght@400;600;700&display=swap" rel="stylesheet">
<style>
  :root {
    --ink: #111111;
    --paper: #ffffff;
    --backdrop: #ececec;
    --silver: #a9a9a9;
    --silver-light: #d8d8d8;
    --text: #444444;
    --icon: #3fa9d6;
  }
  * { box-sizing: border-box; margin: 0; padding: 0; }
  html, body { width: 1200px; height: 937px; overflow: hidden; }
  body {
    background: var(--backdrop);
    font-family: "Open Sans", Arial, sans-serif;
    color: var(--text);
    position: relative;
  }
  .sheet { position: absolute; background: var(--paper); overflow: hidden; }

  /* brand lockup */
  .brand { display: flex; flex-direction: column; align-items: flex-start; }
  .brand-dot { border-radius: 50%; background: var(--silver); }
  .brand-name {
    font-weight: 700; color: var(--ink); text-transform: uppercase;
    letter-spacing: .04em; line-height: 1.15;
  }

  /* website band */
  .web-band { position: absolute; left: 0; display: flex; align-items: center; }
  .web-pill {
    background: var(--ink); color: var(--paper);
    border-radius: 0 999px 999px 0; display: flex; align-items: center;
    letter-spacing: .16em; font-weight: 400;
  }
  .web-rule { height: 1px; background: var(--silver); flex: 1; }

  /* letterhead with letter */
  .letterhead { left: 185px; top: 68px; width: 388px; height: 544px; }
  .letterhead .brand { position: absolute; left: 38px; top: 44px; }
  .letterhead .brand-dot { width: 30px; height: 30px; margin-bottom: 6px; }
  .letterhead .brand-name { font-size: 9px; width: 110px; }
  .contact { list-style: none; font-size: 4.6px; line-height: 7px; color: #666; }
  .contact li { display: flex; align-items: center; gap: 3px; }
  .contact svg { width: 5px; height: 5px; flex: none; }
  .letterhead .contact { position: absolute; left: 302px; top: 22px; }
  .letter { position: absolute; left: 38px; top: 137px; width: 296px; font-size: 5px; line-height: 6.6px; color: #555; }
  .letter p { margin-bottom: 8px; }
  .letter .date { margin-bottom: 8px; }
  .letter .salute strong { color: #222; }
  .letter .gap { margin-bottom: 22px; }
  .signature { width: 32px; height: 22px; background: var(--silver-light); margin: 4px 0 6px; }
  .signer strong { color: #222; }
  .letterhead .web-band { top: 496px; width: 365px; }
  .letterhead .web-pill { width: 176px; height: 22px; padding-left: 16px; font-size: 8px; }

  /* blank letterhead with watermark */
  .letterhead-blank { left: 636px; top: 40px; width: 460px; height: 577px; }
  .watermark {
    position: absolute; left: 60px; top: 90px; width: 340px; height: 340px; border-radius: 50%;
    background: radial-gradient(circle, #ffffff 0%, #f1f1f1 55%, rgba(255,255,255,0) 72%);
  }
  .letterhead-blank .brand { position: absolute; left: 42px; top: 456px; }
  .letterhead-blank .brand-dot { width: 34px; height: 34px; margin-bottom: 6px; }
  .letterhead-blank .brand-name { font-size: 10px; width: 130px; }
  .letterhead-blank .web-band { top: 525px; width: 457px; }
  .letterhead-blank .web-pill { width: 213px; height: 23px; padding-left: 28px; font-size: 9.5px; }

  /* business cards */
  .card { width: 177px; height: 100px; border-radius: 8px; }
  .card-front { left: 45px; top: 660px; }
  .card-front .brand { position: absolute; left: 88px; top: 12px; flex-direction: row; align-items: center; gap: 4px; }
  .card-front .brand-dot { width: 14px; height: 14px; }
  .card-front .brand-name { font-size: 5.6px; width: 70px; }
  .card-front .name-band {
    position: absolute; left: 0; top: 40px; width: 76px; height: 19px; background: var(--ink);
    border-radius: 0 999px 999px 0; color: var(--paper); text-align: center; padding-top: 2px;
  }
  .name-band .person { font-size: 6px; line-height: 8px; display: block; }
  .name-band .role { font-size: 3.6px; letter-spacing: .06em; display: block; }
  .card-front .contact { position: absolute; left: 8px; top: 68px; }
  .card-front .address { position: absolute; left: 104px; top: 78px; font-size: 4.6px; line-height: 6px; color: #666; }
  .card-back { left: 45px; top: 785px; }
  .card-back .brand { position: absolute; left: 56px; top: 38px; align-items: center; }
  .card-back .brand-dot { width: 16px; height: 16px; margin-bottom: 3px; }
  .card-back .brand-name { font-size: 6px; text-align: center; width: 70px; }

  /* envelopes */
  .envelope { width: 431px; height: 208px; }
  .envelope-front { left: 265px; top: 672px; }
  .envelope-front .brand { position: absolute; left: 8px; top: 134px; flex-direction: row; align-items: center; gap: 5px; }
  .envelope-front .brand-dot { width: 24px; height: 24px; }
  .envelope-front .brand-name { font-size: 8px; width: 120px; }
  .envelope-front .web-band { top: 166px; width: 431px; }
  .envelope-front .web-pill { width: 200px; height: 22px; padding-left: 26px; font-size: 9px; }
  .envelope-back { left: 737px; top: 672px; }
  .flap {
    position: absolute; left: 0; top: 0; width: 100%; height: 72px; background: var(--ink);
    border-radius: 0 0 48px 48px; color: var(--paper); text-align: center;
    font-size: 12px; letter-spacing: .18em; padding-top: 26px;
  }
  .envelope-back .brand { position: absolute; left: 150px; top: 106px; align-items: center; }
  .envelope-back .brand-dot { width: 30px; height: 30px; margin-bottom: 5px; }
  .envelope-back .brand-name { font-size: 9px; text-align: center; width: 130px; }
</style>
</head>
<body>

<svg width="0" height="0" style="position:absolute" aria-hidden="true">
  <symbol id="i-pin" viewBox="0 0 10 10"><path d="M5 0a3.5 3.5 0 0 0-3.5 3.5C1.5 6 5 10 5 10s3.5-4 3.5-6.5A3.5 3.5 0 0 0 5 0z" fill="#3fa9d6"/></symbol>
  <symbol id="i-phone" viewBox="0 0 10 10"><path d="M2 1l2 2-1 1.2a6 6 0 0 0 2.8 2.8L7 6l2 2-1.2 1.5C4.5 9.5.5 5.5.5 2.2z" fill="#3fa9d6"/></symbol>
  <symbol id="i-mail" viewBox="0 0 10 10"><rect x="0.5" y="2" width="9" height="6" rx="1" fill="#3fa9d6"/></symbol>
  <symbol id="i-web" viewBox="0 0 10 10"><circle cx="5" cy="5" r="4.5" fill="#3fa9d6"/></symbol>
</svg>

<!-- Letterhead with letter -->
<section class="sheet letterhead">
  <div class="brand">
    <span class="brand-dot"></span>
    <span class="brand-name">Brenmoor Security Services Ltd.</span>
  </div>
  <ul class="contact">
    <li><svg><use href="#i-pin"/></svg>48 Kingsway Road,</li>
    <li>&nbsp;&nbsp;Eastbridge, UK</li>
    <li><svg><use href="#i-phone"/></svg>+44 (0)20 7946 0321</li>
    <li><svg><use href="#i-mail"/></svg>info@brenmoorsecurity.com</li>
    <li><svg><use href="#i-web"/></svg>www.brenmoorsecurity.com</li>
  </ul>
  <div class="letter">
    <p class="date">July 2, 2012</p>
    <p class="salute"><strong>Dear Client,</strong><br>ABC Building, def St., Country Name</p>
    <p>Thank you for your interest in our services. We provide trained guards, site patrols and alarm response for offices, shops and private homes. Every team is vetted, licensed and briefed before duty. Our control room runs day and night, so help is never far away when you need it. We look forward to working with you soon.</p>
    <p class="gap">Please find our full proposal enclosed with this letter, along with a short outline of rates and terms.</p>
    <p>Our staff complete regular training in first aid, conflict handling and fire safety. We review each site with the client and agree clear duties, patrol times and reporting steps. Monthly reports keep you informed, and a named manager is always on hand to answer questions or adjust cover at short notice.</p>
    <p>Best Regards,</p>
    <div class="signature" role="img" aria-label="Handwritten signature of the director"></div>
    <p class="signer"><strong>Daniel Hart</strong><br>Director<br><br>ABC Building, def St., Country Name</p>
  </div>
  <div class="web-band"><span class="web-pill">www.brenmoorsecurity.com</span><span class="web-rule"></span></div>
</section>

<!-- Blank letterhead with watermark -->
<section class="sheet letterhead-blank">
  <div class="watermark" role="img" aria-label="Faint company watermark"></div>
  <div class="brand">
    <span class="brand-dot"></span>
    <span class="brand-name">Brenmoor Security Services Ltd.</span>
  </div>
  <div class="web-band"><span class="web-pill">www.brenmoorsecurity.com</span><span class="web-rule"></span></div>
</section>

<!-- Business card front -->
<section class="sheet card card-front">
  <div class="brand">
    <span class="brand-dot"></span>
    <span class="brand-name">Brenmoor Security Services Ltd.</span>
  </div>
  <div class="name-band">
    <span class="person">Owen Carter</span>
    <span class="role">GENERAL MANAGER</span>
  </div>
  <ul class="contact">
    <li><svg><use href="#i-phone"/></svg>+44 (0)20 7946 0321</li>
    <li><svg><use href="#i-mail"/></svg>info@brenmoorsecurity.com</li>
    <li><svg><use href="#i-web"/></svg>www.brenmoorsecurity.com</li>
  </ul>
  <p class="address">48 Kingsway Road,<br>Eastbridge, UK</p>
</section>

<!-- Business card back -->
<section class="sheet card card-back">
  <div class="brand">
    <span class="brand-dot"></span>
    <span class="brand-name">Brenmoor Security Services Ltd.</span>
  </div>
</section>

<!-- Envelope front -->
<section class="sheet envelope envelope-front">
  <div class="brand">
    <span class="brand-dot"></span>
    <span class="brand-name">Brenmoor Security Services Ltd.</span>
  </div>
  <div class="web-band"><span class="web-pill">www.brenmoorsecurity.com</span><span class="web-rule"></span></div>
</section>

<!-- Envelope back -->
<section class="sheet envelope envelope-back">
  <div class="flap">www.brenmoorsecurity.com</div>
  <div class="brand">
    <span class="brand-dot"></span>
    <span class="brand-name">Brenmoor Security Services Ltd.</span>
  </div>
</section>

</body>
</html>
```